Front page of Orthodox Christian Monastery Website

I am attaching a couple of versions of design that was already created for the front page of the website. You can grab the same pictures and titles (do not need to know the Russian language) to create your own version of design.
Background: Monastery website contains sermons, stories about monastery life, monastery music of the sisterhood.
Main principles of the design:
1. Various materials/sermons/music have to be clearly visible immediately to the site visitor.
2. Text descriptions to photos should be using font with a good contrast, highly clickable and easily readable.
3. Every article should have a photo or a quality picture (use those in the sample) that will convey something about it.
4. On the top, there will be a menu, which will be a line of words (just use generic words for now).
5. Design should reflect Christian Orthodox themes and fonts.
Updates

Target Market(s)

Orthodox Christian believers around the world and those that are interested in Orthodox Christianity

Number of Pages Required

1 page

Font styles to use
Serif

Colors

Designer to choose colors to be used in the design.

Requirements
Must have
• In the project description
Nice to have
• for some ideas see a popular Orthodox Christian website:
• www.verenskaya-lampada.ru
• We don't want to copy it, but it could give ideas.
Should not have
• Should not be overly complex

```html
<!DOCTYPE html>
<html lang="en">
<head>
<meta charset="utf-8">
<title>Orthodox Christian Monastery</title>
<link href="https://fonts.googleapis.com/css2?family=Lato:wght@400;700;900&display=swap" rel="stylesheet">
<style>
:root{
  --teal:#1b6b5e;
  --teal-text:#1d6f62;
  --orange:#f0a30a;
  --ink:#2b2b2b;
  --body:#555;
  --line:#e2e2e2;
  --topbar:#efefef;
  --footer:#2a2a2a;
  --white:#fff;
}
*{box-sizing:border-box;margin:0;padding:0}
html,body{width:1200px;height:2715px;overflow:hidden}
body{font-family:'Lato',sans-serif;color:var(--ink);background:var(--white);position:relative}
a{color:inherit;text-decoration:none}
.wrap{width:1052px;margin-left:74px;position:relative}

.topbar{height:49px;background:var(--topbar)}
.topbar .wrap{display:flex;justify-content:space-between;align-items:center;height:49px}
.social{display:flex;gap:10px;align-items:center}
.social span{width:13px;height:13px;border-radius:50%;background:#333;display:block}
.lang{display:flex;align-items:center;gap:8px;font-size:11px;font-weight:700}
.lang .flag{width:22px;height:13px;background:#c8102e;border:3px solid #012169}

.header{height:98px}
.header .wrap{display:flex;align-items:center;justify-content:space-between;height:98px}
.brand{font-weight:700;font-size:22px;line-height:26px;color:#444;letter-spacing:.3px}
.search{display:flex;width:690px;height:41px;border:1px solid #ccc}
.search input{flex:1;border:0;padding:0 14px;font:14px 'Lato',sans-serif;color:#333}
.search button{width:48px;border:0;background:#222;display:flex;align-items:center;justify-content:center}

.nav{height:58px;background:var(--teal)}
.nav ul{list-style:none;display:flex;height:58px;align-items:center;gap:0}
.nav li{font-size:12px;font-weight:700;color:var(--white);margin-right:53px}
.nav li:first-child{margin-left:2px}

.photo{position:relative;overflow:hidden}
.caption{position:absolute;left:0;right:0;bottom:0;padding:60px 24px 22px;background:linear-gradient(transparent,rgba(0,0,0,.82));color:var(--white)}
.caption h3{font-size:15px;font-weight:700;margin-bottom:8px}
.caption p{font-size:13.5px;line-height:23px}
.more{color:var(--orange);font-weight:700}

.hero{display:flex;gap:15px;margin-top:20px;height:389px}
.hero .photo{width:706px;height:389px;background:radial-gradient(ellipse at 45% 40%,#4d7cb8 0 25%,#7a5238 45%,#3d2a1e 100%)}
.arrow{position:absolute;top:165px}
.about{width:331px;border:3px solid #ddd;background:#f4f4f4;padding:20px 18px}
.about h2{font-size:23px;font-weight:400;line-height:28px;margin-bottom:14px}
.about p{font-size:13.5px;line-height:26px;color:var(--body);margin-bottom:10px}
.btn{display:inline-block;background:var(--teal);color:var(--white);font-size:11px;font-weight:700;padding:11px 34px;margin-top:6px}

.divider{height:1px;background:var(--line);margin-top:36px}
.sec-head{display:flex;justify-content:space-between;align-items:center;margin-top:24px;height:28px}
.sec-head h2{font-size:23px;font-weight:400}
.view{border:2px solid var(--teal);color:var(--teal);font-size:10.5px;font-weight:700;padding:6px 32px}

.feature{display:flex;gap:14px;margin-top:22px}
.feature .photo{width:602px;height:418px}
.side{display:flex;flex-direction:column;gap:32px;width:436px}
.side .item{display:flex;gap:27px;height:118px}
.thumb{width:166px;height:118px;flex:none}
.item h4,.card h4{font-size:14.5px;font-weight:900;color:var(--teal-text);line-height:21px}
.item p,.card p{font-size:13.5px;line-height:23px;color:var(--body);margin-top:4px}
.item h4{margin-top:-2px}

.cards{display:flex;gap:30px;margin-top:27px}
.card{width:331px}
.card .img{height:180px;margin-bottom:20px}
.card p{margin-top:4px}

.music{display:flex;gap:50px;margin-top:22px}
.music .side{width:402px;gap:32px}
.music .photo{width:600px;height:417px;background:linear-gradient(160deg,#4a4a4a,#1b1b1b 55%,#6d2020)}

.footer{position:absolute;left:0;top:2449px;width:1200px;height:266px;background:var(--footer);color:#ddd}
.footer .wrap{display:flex;padding-top:40px}
.f-brand{width:331px;padding-top:24px}
.f-brand .brand{color:#e5e5e5}
.f-brand p{font-size:12px;line-height:21px;margin-top:22px}
.f-brand .social{margin-top:14px;gap:16px}
.f-brand .social span{width:18px;height:18px;background:#ddd}
.f-col{width:245px}
.f-col h5,.signup h5{font-size:13px;font-weight:700;color:var(--white);margin-bottom:13px}
.f-col li{list-style:none;font-size:12px;line-height:27.5px;color:#ccc}
.signup{width:235px}
.signup input{display:block;width:235px;height:36px;border:0;margin-bottom:9px;padding:0 12px;font:700 11px 'Lato',sans-serif;color:#333}
.signup button{margin-left:141px;margin-top:4px;width:94px;height:36px;border:0;background:var(--orange);color:var(--white);font:700 12px 'Lato',sans-serif}
</style>
</head>
<body>

<div class="topbar">
  <div class="wrap">
    <div class="social" aria-label="Social links"><span></span><span></span><span></span><span></span><span></span></div>
    <div class="lang"><span class="flag"></span>EN
      <svg width="8" height="6" viewBox="0 0 8 6"><path d="M1 1l3 3 3-3" stroke="#333" fill="none" stroke-width="1.4"/></svg>
    </div>
  </div>
</div>

<header class="header">
  <div class="wrap">
    <div class="brand">ORTHODOX CHRISTIAN<br>MONASTERY</div>
    <form class="search">
      <input type="text" placeholder="Search...">
      <button type="button" aria-label="Search">
        <svg width="18" height="18" viewBox="0 0 18 18"><circle cx="7.5" cy="7.5" r="5.5" stroke="#fff" stroke-width="2" fill="none"/><path d="M11.5 11.5l5 5" stroke="#fff" stroke-width="2.4"/></svg>
      </button>
    </form>
  </div>
</header>

<nav class="nav">
  <ul class="wrap">
    <li>HOME</li><li>SERMONS</li><li>ABOUT MONASTERY LIFE</li><li>MONASTERY MUSIC</li><li>ONLINE MAGZINE</li><li>NEWS</li>
  </ul>
</nav>

<main>
  <section class="wrap hero">
    <div class="photo" role="img" aria-label="Orthodox icon of the Resurrection">
      <svg class="arrow" style="left:8px" width="20" height="30" viewBox="0 0 20 30"><path d="M15 3L4 15l11 12" stroke="#fff" stroke-width="3" fill="none"/></svg>
      <svg class="arrow" style="right:8px" width="20" height="30" viewBox="0 0 20 30"><path d="M5 3l11 12L5 27" stroke="#fff" stroke-width="3" fill="none"/></svg>
      <div class="caption">
        <h3>EXCEPTEUR SINT OCCAECAT CUPIDATAT NON ALIQUAM</h3>
        <p>Lanventore veritatis et quasi &nbsp;architecto beatae vitae dicta sunt explicaboenim qui ratione &nbsp;voluptatem sequi nesciunt deserunt mollit anim id est laborum...<span class="more">Read More</span></p>
      </div>
    </div>
    <aside class="about">
      <h2>ABOUT<br>MONASTERY LIFE</h2>
      <p>Lanventore veritatis et quasi architecto beatae vitae dicta sunt explicabo. Nemo enim ipsam voluptatem quia voluptas sit aspernatur aut odit aut fugit..</p>
      <p>Architecto beatae vitae dicta sunt explicabo. Nemo enim ipsam voluptatem quia voluptas sit aspernatur aut odit aut fugit unde omnis iste natus error..</p>
      <a class="btn">READ MORE</a>
    </aside>
  </section>

  <section class="wrap">
    <div class="divider"></div>
    <div class="sec-head"><h2>SERMONS</h2><a class="view">VIEW ALL</a></div>
    <div class="feature">
      <div class="photo" role="img" aria-label="Priest reading scripture to a congregation" style="background:linear-gradient(135deg,#b9a58a,#6b4a35 50%,#2b211b)">
        <div class="caption">
          <h3>EXCEPTEUR SINT OCCAECAT CUPIDATAT NON ALIQUAM</h3>
          <p>Lanventore veritatis et quasi &nbsp;architecto beatae vitae dicta sunt explicaboenim qui ratione &nbsp;voluptatem sequi nesciunt deserunt mollit anim id est laborum...<span class="more">Read More</span></p>
        </div>
      </div>
      <div class="side">
        <div class="item"><div class="thumb" role="img" aria-label="Statue by the sea" style="background:linear-gradient(#b8c4cc,#8a7258)"></div>
          <div><h4>EXCEPTEUR SINT OCCAECAT CUPIDATAT NON</h4><p>Lanventore veritatis et quasi architecto beatae vitae dicta sunt explicaboenim..<span class="more">Read More</span></p></div></div>
        <div class="item"><div class="thumb" role="img" aria-label="Candles lit in church" style="background:linear-gradient(#2a3a4a,#c8843a 60%,#3a2a22)"></div>
          <div><h4>EXCEPTEUR SINT OCCAECAT CUPIDATAT NON</h4><p>Lanventore veritatis et quasi architecto beatae vitae dicta sunt explicaboenim..<span class="more">Read More</span></p></div></div>
        <div class="item"><div class="thumb" role="img" aria-label="Cross against a bright sky" style="background:linear-gradient(135deg,#f3e4c2,#d9c6a0 50%,#b8ad9a)"></div>
          <div><h4>EXCEPTEUR SINT OCCAECAT CUPIDATAT NON</h4><p>Lanventore veritatis et quasi architecto beatae vitae dicta sunt explicaboenim..<span class="more">Read More</span></p></div></div>
      </div>
    </div>
    <div class="cards">
      <article class="card"><div class="img" role="img" aria-label="Interior of a cathedral" style="background:linear-gradient(#6b5a3a,#2a2418)"></div>
        <h4>EXCEPTEUR SINT OCCAECAT CUPIDATAT NON ALIQUAM</h4><p>Lanventore veritatis et quasi &nbsp;architecto beatae vitae dicta sunt explicaboenim qui ratione voluptatem sequi nesciunt deserunt mollit anim id est laborum...<span class="more">Read More</span></p></article>
      <article class="card"><div class="img" role="img" aria-label="Painted church fresco" style="background:linear-gradient(135deg,#8a8aa0,#7a5a4a 55%,#4a3a34)"></div>
        <h4>EXCEPTEUR SINT OCCAECAT CUPIDATAT NON ALIQUAM</h4><p>Lanventore veritatis et quasi &nbsp;architecto beatae vitae dicta sunt explicaboenim qui ratione voluptatem sequi nesciunt deserunt mollit anim id est laborum...<span class="more">Read More</span></p></article>
      <article class="card"><div class="img" role="img" aria-label="Icon on a red altar cloth" style="background:linear-gradient(#b8913a,#b0202a 60%,#7a1418)"></div>
        <h4>EXCEPTEUR SINT OCCAECAT CUPIDATAT NON ALIQUAM</h4><p>Lanventore veritatis et quasi &nbsp;architecto beatae vitae dicta sunt explicaboenim qui ratione voluptatem sequi nesciunt deserunt mollit anim id est laborum...<span class="more">Read More</span></p></article>
    </div>
  </section>

  <section class="wrap">
    <div class="divider" style="margin-top:48px"></div>
    <div class="sec-head"><h2>MONASTERY MUSIC OF THE SISTERHOOD</h2><a class="view">VIEW ALL</a></div>
    <div class="music">
      <div class="side">
        <div class="item"><div class="thumb" role="img" aria-label="Church bells" style="background:linear-gradient(135deg,#a04a3a,#6a2a22)"></div>
          <div><h4>EXCEPTEUR SINT OCCAECAT CUPIDATAT NON</h4><p>Lanventore veritatis et quasi architecto beatae vitae dicta sunt explicaboenim..<span class="more">Read More</span></p></div></div>
        <div class="item"><div class="thumb" role="img" aria-label="Open book of chants" style="background:linear-gradient(135deg,#e0dcd2,#8a7a64)"></div>
          <div><h4>EXCEPTEUR SINT OCCAECAT CUPIDATAT NON</h4><p>Lanventore veritatis et quasi architecto beatae vitae dicta sunt explicaboenim..<span class="more">Read More</span></p></div></div>
        <div class="item"><div class="thumb" role="img" aria-label="Illuminated manuscript" style="background:linear-gradient(135deg,#c9b28a,#9a5a3a)"></div>
          <div><h4>EXCEPTEUR SINT OCCAECAT CUPIDATAT NON</h4><p>Lanventore veritatis et quasi architecto beatae vitae dicta sunt explicaboenim..<span class="more">Read More</span></p></div></div>
      </div>
      <div class="photo" role="img" aria-label="Choir of nuns singing from music books">
        <div class="caption">
          <h3>EXCEPTEUR SINT OCCAECAT CUPIDATAT NON ALIQUAM</h3>
          <p>Lanventore veritatis et quasi &nbsp;architecto beatae vitae dicta sunt explicaboenim qui ratione &nbsp;voluptatem sequi nesciunt deserunt mollit anim id est laborum...<span class="more">Read More</span></p>
        </div>
      </div>
    </div>
    <div class="cards" style="margin-top:30px">
      <article class="card"><div class="img" role="img" aria-label="Women singing in a choir" style="background:linear-gradient(135deg,#5a4a44,#2a2222 60%,#8a2a2a)"></div>
        <h4>EXCEPTEUR SINT OCCAECAT CUPIDATAT NON ALIQUAM</h4><p>Lanventore veritatis et quasi &nbsp;architecto beatae vitae dicta sunt explicaboenim qui ratione voluptatem sequi nesciunt deserunt mollit anim id est laborum...<span class="more">Read More</span></p></article>
      <article class="card"><div class="img" role="img" aria-label="Gilded church organ" style="background:linear-gradient(#8a7a6a,#b08a3a 55%,#5a4022)"></div>
        <h4>EXCEPTEUR SINT OCCAECAT CUPIDATAT NON ALIQUAM</h4><p>Lanventore veritatis et quasi &nbsp;architecto beatae vitae dicta sunt explicaboenim qui ratione voluptatem sequi nesciunt deserunt mollit anim id est laborum...<span class="more">Read More</span></p></article>
      <article class="card"><div class="img" role="img" aria-label="Orchestra in a monastery courtyard" style="background:linear-gradient(#9a8a74,#5a4a3a 60%,#2a2420)"></div>
        <h4>EXCEPTEUR SINT OCCAECAT CUPIDATAT NON ALIQUAM</h4><p>Lanventore veritatis et quasi &nbsp;architecto beatae vitae dicta sunt explicaboenim qui ratione voluptatem sequi nesciunt deserunt mollit anim id est laborum...<span class="more">Read More</span></p></article>
    </div>
  </section>
</main>

<footer class="footer">
  <div class="wrap">
    <div class="f-brand">
      <div class="brand">ORTHODOX CHRISTIAN<br>MONASTERY</div>
      <p>Copyright © 2018, Company Name<br>All Right reserved</p>
      <div class="social"><span></span><span></span><span></span><span></span><span></span></div>
    </div>
    <div class="f-col"><h5>QUICK LINKS</h5><ul><li>Home</li><li>Sermons</li><li>About monastery life</li><li>Monastery music</li><li>Online Magzine</li><li>News</li></ul></div>
    <div class="f-col" style="width:233px"><h5>RESOURCES</h5><ul><li>Home</li><li>Sermons</li><li>About monastery life</li><li>Monastery music</li><li>Online Magzine</li><li>News</li></ul></div>
    <form class="signup"><h5>EMAIL SIGN UP</h5>
      <input type="text" placeholder="ENTER NAME">
      <input type="email" placeholder="ENTER EMAIL">
      <button type="button">SIGN UP</button>
    </form>
  </div>
</footer>

</body>
</html>
```